New Business Card for our Indoor Golf Training Facility

We are looking for designs for a new business card for our indoor golf training facility. Attached is our logo, our logo with our slogan, and here is our elevator pitch (What makes us different from the others) not sure if all the info will fit on one card, maybe you can condense the elevator pitch? here is the info

Elevator Pitch
We work with serious golfers and those that want to be serious golfers…
to make you better, faster, at all phases of the game…
We use the same state-of-the-art technology as professional golfers…
which produces data sets that shows your improvement in real time.
Our facility is available 24/7 to our members, which allows you to improve on your time.

our website: www.birchpinlinks.com

Target Market(s)

Golfers

Font styles to use
Serif
Sans Serif

Colors
ec1f27
f59195
fbd4d5
919191
d3d3d3
1b1b1b

Requirements
Must have
• our logo or our logo with the slogan, elevator pitch (can be condensed or shortened)

```html
<!DOCTYPE html>
<html lang="en">
<head>
<meta charset="utf-8">
<title>Birch Pin Links – Business Card</title>
<link rel="stylesheet" href="https://fonts.googleapis.com/css2?family=Roboto:wght@400;500;700;900&family=Roboto+Condensed:wght@400;700&display=swap">
<style>
  :root {
    --red: #ec3a35;
    --red-soft: #f59195;
    --grey: #8a8a8a;
    --grey-dark: #7b7b7b;
    --grey-light: #d3d3d3;
    --paper: #f4f4f4;
    --ink: #1b1b1b;
    --white: #ffffff;
    --backdrop: #e9e7e4;
  }
  * { margin: 0; padding: 0; box-sizing: border-box; }
  html, body { width: 1200px; height: 950px; overflow: hidden; }
  body {
    background: var(--backdrop);
    font-family: "Roboto", Arial, sans-serif;
    position: relative;
  }
  .card {
    position: absolute;
    left: 250px;
    width: 700px;
    height: 400px;
    border-radius: 26px;
    overflow: hidden;
    box-shadow: 0 10px 28px rgba(0,0,0,0.25);
  }
  /* Front */
  .card--front { top: 40px; background: var(--paper); }
  .front__brand {
    position: absolute; left: 0; top: 0; width: 100%; height: 215px;
    display: flex; align-items: center; padding-left: 60px; gap: 26px;
  }
  .brand__circle {
    width: 110px; height: 110px; border-radius: 50%;
    border: 9px solid var(--red); flex: none;
  }
  .brand__name {
    color: var(--red); font-weight: 900; font-size: 58px; line-height: 1;
    letter-spacing: -0.5px;
  }
  .brand__slogan {
    color: var(--red); font-size: 21px; margin-top: 8px; font-weight: 400;
  }
  .front__name-band {
    position: absolute; left: 0; top: 215px; width: 100%; height: 70px;
    background: var(--grey);
    padding-left: 250px; color: var(--white);
    display: flex; flex-direction: column; justify-content: center;
  }
  .person__name { font-size: 25px; font-weight: 500; letter-spacing: 0.5px; }
  .person__title { font-size: 17px; color: #efefef; margin-top: 2px; }
  .front__divider {
    position: absolute; left: 0; top: 285px; width: 100%; height: 5px;
    background: var(--white);
  }
  .front__contact-band {
    position: absolute; left: 0; top: 290px; width: 100%; height: 110px;
    background: var(--red); color: var(--white);
    display: flex; justify-content: space-between; align-items: center;
    padding: 0 50px 0 40px;
  }
  .contact-list { list-style: none; font-size: 19px; line-height: 1.45; }
  .contact-list li { display: flex; align-items: center; gap: 12px; }
  .contact-list svg { width: 16px; height: 16px; fill: var(--white); flex: none; }
  .address { font-size: 19px; line-height: 1.4; text-align: right; font-style: normal; }
  /* Back */
  .card--back {
    top: 500px; background: var(--grey-dark); color: var(--white);
    display: flex; align-items: center; padding: 0 50px; gap: 40px;
  }
  .back__pitch { flex: 1; }
  .pitch__heading {
    font-family: "Roboto Condensed", Arial, sans-serif;
    font-weight: 700; font-size: 28px; letter-spacing: 0.5px; margin-bottom: 14px;
  }
  .pitch__text {
    font-family: "Roboto Condensed", Arial, sans-serif;
    font-size: 16.5px; line-height: 1.55;
  }
  .back__mark {
    flex: none; display: flex; flex-direction: column; align-items: center; gap: 14px;
  }
  .mark__circle {
    width: 150px; height: 150px; border-radius: 50%;
    border: 10px solid var(--white);
  }
  .mark__name { font-weight: 900; font-size: 24px; color: var(--white); }
</style>
</head>
<body>
  <section class="card card--front" aria-label="Business card front">
    <div class="front__brand">
      <div class="brand__circle"></div>
      <div>
        <div class="brand__name">Birch Pin Links</div>
        <div class="brand__slogan">Par Is Good. Birdie Is Better. Be Better.</div>
      </div>
    </div>
    <div class="front__name-band">
      <div class="person__name">DANA WHITFIELD</div>
      <div class="person__title">CEO/Founder</div>
    </div>
    <div class="front__divider"></div>
    <div class="front__contact-band">
      <ul class="contact-list">
        <li><svg viewBox="0 0 16 16"><path d="M3.5 1l3 3-2 2c1 2 3.5 4.5 5.5 5.5l2-2 3 3-2.5 2.5C7 14 2 9 1 3.5z"/></svg>555-404-1862</li>
        <li><svg viewBox="0 0 16 16"><path d="M1 3h14v10H1z M1 3l7 6 7-6" fill="none" stroke="#fff" stroke-width="1.6"/></svg>info@birchpinlinks.com</li>
        <li><svg viewBox="0 0 16 16"><circle cx="8" cy="8" r="6.5" fill="none" stroke="#fff" stroke-width="1.6"/><path d="M1.5 8h13M8 1.5c-3 3.5-3 9.5 0 13M8 1.5c3 3.5 3 9.5 0 13" fill="none" stroke="#fff" stroke-width="1.2"/></svg>www.birchpinlinks.com</li>
      </ul>
      <address class="address">1480 W. Alder Rd<br>Unit B4<br>Fairview, OH 45099</address>
    </div>
  </section>

  <section class="card card--back" aria-label="Business card back">
    <div class="back__pitch">
      <h2 class="pitch__heading">ELEVATOR PITCH:</h2>
      <p class="pitch__text">
        We work with serious golfers and those that want to be serious golfers…<br>
        to make you better, faster, at all phases of the game…<br>
        We use the same state-of-the-art technology as professional golfers…<br>
        which produces data sets that shows your improvement in real time.<br>
        Available 24/7 to our members, which allows you to improve on your time.
      </p>
    </div>
    <div class="back__mark">
      <div class="mark__circle"></div>
      <div class="mark__name">Birch Pin Links</div>
    </div>
  </section>
</body>
</html>
```